Working Capital graphics

Our business advisory firm requires 9 images to be re-created and improved in the branding of our business.

The 9 images have been uploaded below and the colours and branding of the business can be found at the website www.tallowmereadvisory.com.au

```html
<!DOCTYPE html>
<html lang="en">
<head>
<meta charset="utf-8">
<title>Working Capital Cycles</title>
<link rel="stylesheet" href="https://fonts.googleapis.com/css2?family=Jost:wght@500;600;700&display=swap">
<style>
  :root {
    --navy: #143a82;
    --sky: #0bb0f1;
    --orange: #f7931e;
    --white: #ffffff;
    --frame: #d3d3d3;
  }
  html, body { margin: 0; padding: 0; overflow: hidden; background: var(--white); }
  .canvas { width: 1200px; height: 1166px; display: block; }
  .canvas text { font-family: "Jost", sans-serif; font-weight: 600; text-anchor: middle; }
  .step-sm { fill: var(--navy); font-size: 15.5px; letter-spacing: 0.6px; }
  .step-lg { fill: var(--navy); font-size: 19.5px; letter-spacing: 0.6px; }
  .hub-title { fill: var(--white); font-size: 33px; letter-spacing: 0.8px; }
  .wedge-label { fill: var(--white); font-size: 31px; letter-spacing: 1px; }
  .banner { fill: var(--navy); }
  .banner-label { fill: var(--white); font-size: 33px; letter-spacing: 1px; }
  .hub-ring { fill: none; stroke: var(--navy); stroke-width: 4; }
  .hub-core { fill: var(--sky); }
  .flow-arrow { stroke: var(--orange); stroke-width: 3; fill: none; }
  .branch-arrow { stroke: var(--navy); stroke-width: 6; fill: none; }
  .capital-wedge { fill: var(--orange); }
  .wedge-divider { stroke: var(--white); stroke-width: 3; fill: none; }
  .frame { fill: none; stroke: var(--frame); stroke-width: 8; }
</style>
</head>
<body>
<svg class="canvas" viewBox="0 0 1928 1874" xmlns="http://www.w3.org/2000/svg" role="img" aria-label="Working capital cycles: Customer to Cash, Forecast to Fulfillment and Purchase to Pay">
  <defs>
    <marker id="tip-orange" viewBox="0 0 10 10" refX="7" refY="5" markerWidth="4" markerHeight="4" orient="auto">
      <path d="M0,0 L10,5 L0,10 L3,5 z" fill="#f7931e"/>
    </marker>
    <marker id="tip-navy" viewBox="0 0 10 10" refX="6" refY="5" markerWidth="4" markerHeight="4" orient="auto">
      <path d="M0,0 L10,5 L0,10 L3,5 z" fill="#143a82"/>
    </marker>
  </defs>

  <rect class="frame" x="4" y="4" width="1920" height="1866"/>

  <!-- Revenue management cycle -->
  <g class="cycle revenue">
    <circle class="hub-ring" cx="431" cy="423" r="155"/>
    <circle class="hub-core" cx="431" cy="423" r="140"/>
    <text class="hub-title" x="431" y="414">REVENUE</text>
    <text class="hub-title" x="431" y="449">MANAGEMENT</text>

    <text class="step-sm"><tspan x="430" y="176">CUSTOMER</tspan><tspan x="430" y="194">STRATEGY</tspan></text>
    <text class="step-sm"><tspan x="570" y="209">SALES</tspan><tspan x="570" y="227">MANAGEMENT</tspan></text>
    <text class="step-sm"><tspan x="640" y="298">RISK</tspan><tspan x="640" y="315">MANAGEMENT</tspan></text>
    <text class="step-sm"><tspan x="670" y="406">CONTRACT</tspan><tspan x="670" y="424">MANAGEMENT</tspan></text>
    <text class="step-sm"><tspan x="652" y="525">SALES ORDER</tspan><tspan x="652" y="542">PROCESSING</tspan></text>
    <text class="step-sm"><tspan x="570" y="623">CREDIT</tspan><tspan x="570" y="641">CHECK</tspan></text>
    <text class="step-sm"><tspan x="442" y="660">ORDER</tspan><tspan x="442" y="677">FULFILLMENT</tspan></text>
    <text class="step-sm" x="311" y="636">BILLING</text>
    <text class="step-sm"><tspan x="222" y="539">CUSTOMER</tspan><tspan x="222" y="557">SERVICE</tspan></text>
    <text class="step-sm"><tspan x="189" y="419">CASH</tspan><tspan x="189" y="437">COLLECTION</tspan></text>
    <text class="step-sm"><tspan x="221" y="290">RECEIPT &amp;</tspan><tspan x="221" y="308">ALLOCATION</tspan><tspan x="221" y="326">OF CASH</tspan></text>
    <text class="step-sm"><tspan x="309" y="210">CASH</tspan><tspan x="309" y="228">MANAGEMENT</tspan></text>

    <g class="flow" marker-end="url(#tip-orange)">
      <line class="flow-arrow" x1="348" y1="201" x2="383" y2="190" marker-end="url(#tip-orange)"/>
      <line class="flow-arrow" x1="476" y1="196" x2="508" y2="207" marker-end="url(#tip-orange)"/>
      <line class="flow-arrow" x1="592" y1="243" x2="616" y2="267" marker-end="url(#tip-orange)"/>
      <line class="flow-arrow" x1="655" y1="338" x2="668" y2="370" marker-end="url(#tip-orange)"/>
      <line class="flow-arrow" x1="667" y1="452" x2="658" y2="485" marker-end="url(#tip-orange)"/>
      <line class="flow-arrow" x1="625" y1="571" x2="601" y2="596" marker-end="url(#tip-orange)"/>
      <line class="flow-arrow" x1="530" y1="645" x2="499" y2="661" marker-end="url(#tip-orange)"/>
      <line class="flow-arrow" x1="383" y1="663" x2="351" y2="649" marker-end="url(#tip-orange)"/>
      <line class="flow-arrow" x1="277" y1="603" x2="258" y2="576" marker-end="url(#tip-orange)"/>
      <line class="flow-arrow" x1="206" y1="496" x2="199" y2="463" marker-end="url(#tip-orange)"/>
      <line class="flow-arrow" x1="201" y1="380" x2="207" y2="350" marker-end="url(#tip-orange)"/>
      <line class="flow-arrow" x1="256" y1="268" x2="277" y2="244" marker-end="url(#tip-orange)"/>
    </g>
  </g>

  <!-- Supply chain management cycle -->
  <g class="cycle supply-chain">
    <circle class="hub-ring" cx="1498" cy="429" r="155"/>
    <circle class="hub-core" cx="1498" cy="429" r="141"/>
    <text class="hub-title" x="1498" y="421">SUPPLY CHAIN</text>
    <text class="hub-title" x="1498" y="455">MANAGEMENT</text>

    <text class="step-lg"><tspan x="1498" y="175">SUPPLY</tspan><tspan x="1498" y="197">CHAIN</tspan><tspan x="1498" y="219">STRATEGY</tspan></text>
    <text class="step-lg"><tspan x="1663" y="205">PRODUCT</tspan><tspan x="1663" y="227">RANGE</tspan><tspan x="1663" y="249">MANAGEMENT</tspan></text>
    <text class="step-lg" x="1738" y="347">FORECASTING</text>
    <text class="step-lg"><tspan x="1738" y="473">SALES ORDER</tspan><tspan x="1738" y="495">FORECASTING</tspan></text>
    <text class="step-lg"><tspan x="1676" y="602">PRODUCTION</tspan><tspan x="1676" y="624">SCHEDULING</tspan></text>
    <text class="step-lg"><tspan x="1506" y="659">RAW</tspan><tspan x="1506" y="681">MATERIAL</tspan><tspan x="1506" y="703">PLANNING</tspan></text>
    <text class="step-lg"><tspan x="1330" y="612">PRODUCTION</tspan><tspan x="1330" y="633">PLANNING</tspan></text>
    <text class="step-lg" x="1248" y="482">PRODUCTION</text>
    <text class="step-lg" x="1256" y="356">WAREHOUSING</text>
    <text class="step-lg" x="1338" y="248">DISTRIBUTION</text>

    <line class="flow-arrow" x1="1405" y1="206" x2="1437" y2="190" marker-end="url(#tip-orange)"/>
    <line class="flow-arrow" x1="1555" y1="194" x2="1589" y2="206" marker-end="url(#tip-orange)"/>
    <line class="flow-arrow" x1="1710" y1="278" x2="1728" y2="307" marker-end="url(#tip-orange)"/>
    <line class="flow-arrow" x1="1743" y1="387" x2="1744" y2="420" marker-end="url(#tip-orange)"/>
    <line class="flow-arrow" x1="1732" y1="530" x2="1716" y2="560" marker-end="url(#tip-orange)"/>
    <line class="flow-arrow" x1="1617" y1="663" x2="1584" y2="675" marker-end="url(#tip-orange)"/>
    <line class="flow-arrow" x1="1428" y1="672" x2="1397" y2="656" marker-end="url(#tip-orange)"/>
    <line class="flow-arrow" x1="1275" y1="563" x2="1266" y2="530" marker-end="url(#tip-orange)"/>
    <line class="flow-arrow" x1="1255" y1="428" x2="1260" y2="393" marker-end="url(#tip-orange)"/>
    <line class="flow-arrow" x1="1296" y1="302" x2="1315" y2="273" marker-end="url(#tip-orange)"/>
  </g>

  <!-- Working capital triangle -->
  <g class="capital-triangle">
    <polygon class="capital-wedge" points="968,580 1260,873 676,873"/>
    <line class="wedge-divider" x1="968" y1="580" x2="968" y2="752"/>
    <line class="wedge-divider" x1="968" y1="752" x2="676" y2="873"/>
    <line class="wedge-divider" x1="968" y1="752" x2="1260" y2="873"/>
    <text class="wedge-label" transform="translate(910 724) rotate(-45)">A/R</text>
    <text class="wedge-label" transform="translate(1060 728) rotate(45)">INVENTORY</text>
    <text class="wedge-label" x="968" y="834">A/P</text>

    <line class="branch-arrow" x1="820" y1="697" x2="778" y2="657" marker-end="url(#tip-navy)"/>
    <line class="branch-arrow" x1="1131" y1="697" x2="1173" y2="657" marker-end="url(#tip-navy)"/>
    <line class="branch-arrow" x1="980" y1="898" x2="980" y2="955" marker-end="url(#tip-navy)"/>
  </g>

  <!-- Cycle banners -->
  <rect class="banner" x="243" y="783" width="377" height="83"/>
  <text class="banner-label" x="431" y="836">CUSTOMER TO CASH</text>
  <rect class="banner" x="1312" y="783" width="477" height="83"/>
  <text class="banner-label" x="1550" y="836">FORECAST TO FULFILLMENT</text>

  <!-- Expenditure management cycle -->
  <g class="cycle expenditure">
    <circle class="hub-ring" cx="970" cy="1335" r="155"/>
    <circle class="hub-core" cx="970" cy="1335" r="141"/>
    <text class="hub-title" x="970" y="1326">EXPENDITURE</text>
    <text class="hub-title" x="970" y="1359">MANAGEMENT</text>

    <text class="step-sm"><tspan x="969" y="1071">PURCHASING</tspan><tspan x="969" y="1088">STRATEGY</tspan></text>
    <text class="step-sm"><tspan x="1125" y="1132">BUDGETING &amp;</tspan><tspan x="1125" y="1150">FORECASTING</tspan></text>
    <text class="step-sm"><tspan x="1208" y="1244">ORIGINATING</tspan><tspan x="1208" y="1262">REQUIREMENTS</tspan></text>
    <text class="step-sm"><tspan x="1211" y="1384">SELECTING &amp;</tspan><tspan x="1211" y="1402">NEGOTIATING</tspan></text>
    <text class="step-sm"><tspan x="1144" y="1505">ORDERING &amp;</tspan><tspan x="1144" y="1523">CONTRACTING</tspan></text>
    <text class="step-sm"><tspan x="980" y="1576">RECEIVING &amp;</tspan><tspan x="980" y="1594">EVALUATING</tspan></text>
    <text class="step-sm"><tspan x="813" y="1518">DISCREPANCY</tspan><tspan x="813" y="1536">MANAGEMENT</tspan></text>
    <text class="step-sm"><tspan x="730" y="1408">INVOICE</tspan><tspan x="730" y="1426">PROCESSING</tspan></text>
    <text class="step-sm"><tspan x="726" y="1252">PAYMENT</tspan><tspan x="726" y="1270">ISSUANCE</tspan></text>
    <text class="step-sm"><tspan x="813" y="1125">CASH</tspan><tspan x="813" y="1142">MANAGEMENT</tspan></text>

    <line class="flow-arrow" x1="875" y1="1107" x2="907" y2="1094" marker-end="url(#tip-orange)"/>
    <line class="flow-arrow" x1="1033" y1="1086" x2="1063" y2="1106" marker-end="url(#tip-orange)"/>
    <line class="flow-arrow" x1="1152" y1="1176" x2="1176" y2="1200" marker-end="url(#tip-orange)"/>
    <line class="flow-arrow" x1="1211" y1="1310" x2="1212" y2="1343" marker-end="url(#tip-orange)"/>
    <line class="flow-arrow" x1="1194" y1="1433" x2="1174" y2="1460" marker-end="url(#tip-orange)"/>
    <line class="flow-arrow" x1="1080" y1="1548" x2="1049" y2="1566" marker-end="url(#tip-orange)"/>
    <line class="flow-arrow" x1="901" y1="1577" x2="871" y2="1560" marker-end="url(#tip-orange)"/>
    <line class="flow-arrow" x1="785" y1="1489" x2="767" y2="1458" marker-end="url(#tip-orange)"/>
    <line class="flow-arrow" x1="725" y1="1350" x2="721" y2="1315" marker-end="url(#tip-orange)"/>
    <line class="flow-arrow" x1="752" y1="1202" x2="770" y2="1175" marker-end="url(#tip-orange)"/>
  </g>

  <rect class="banner" x="786" y="1695" width="377" height="83"/>
  <text class="banner-label" x="974" y="1749">PURCHASE TO PAY</text>
</svg>
</body>
</html>
```